ULMIRA card Technical Architecture

Hello everyone ULMIRA: It is a consulting firm in Architecture and Construction. I require a card duplexing, sober, elegant, classic but not boring. Update 1: Use the following data for the card. Name: Gonzalo Pereda Mauricio Villalta Position: COO Twitter: @ulmiraAT Homepage: ulmira-example.com home address not include the participation of all thank you.

Target Market(s)

Construction companies, Architects and Consulting Engineers

Industry/Entity Type

Consulting

Contact Information for Business Card

Los campos que debe tener:
Nombre, Cargo, email, homepage y twitter

Font styles to use
Serif
Sans Serif
Other font styles liked:
• Me gustan playfair display, open sans y roboto, pero estoy sujeto a sus propuestas

Requirements
Must have
• Colors: Present combined proposals in white, red, gray and black Update 1: The two names must be clearly differentiated from the two surnames
Nice to have
• They are free to present their best proposals. I will bring them immediate feedback to the extent you can go see their designs. Complete data for card and logo files will give the winner the

```html
<!DOCTYPE html>
<html lang="es">
<head>
<meta charset="utf-8">
<title>ULMIRA – Tarjeta de presentación</title>
<link rel="stylesheet" href="https://fonts.googleapis.com/css2?family=Montserrat:wght@400;500;700&display=swap">
<style>
  :root{
    --bg:#2b2b2d;
    --red:#b3202a;
    --red-deep:#5e0b10;
    --wine:#6f1016;
    --white:#ffffff;
    --paper-shade:#e9e9ea;
    --ink:#222222;
    --gray:#4a4a4a;
    --rule:#9a9a9a;
    --black:#1c1c1c;
  }
  *{box-sizing:border-box;margin:0;padding:0}
  html,body{width:1200px;height:900px;overflow:hidden;background:var(--bg);font-family:"Montserrat",sans-serif}
  .stage{position:relative;width:1200px;height:900px}
  .card{position:absolute;width:560px;height:320px;border-radius:22px;overflow:hidden;box-shadow:0 18px 40px rgba(0,0,0,.45)}

  /* back (red) side */
  .card--back{left:70px;top:120px;background:radial-gradient(circle at 52% 45%, #c8222c 0%, var(--red) 22%, #7d1016 62%, var(--red-deep) 100%)}
  .card--back .base{position:absolute;inset:0}
  .card--back .brand{position:absolute;left:0;right:0;top:118px;text-align:center;color:var(--white);font-weight:700;font-size:46px;letter-spacing:12px}
  .card--back .social{position:absolute;left:28px;bottom:12px;display:flex;align-items:center;gap:12px;color:var(--ink);font-size:15px}
  .dot{width:12px;height:12px;border-radius:50%;background:var(--red)}

  /* front (white) side */
  .card--front{left:570px;top:480px;background:var(--white)}
  .card--front .base{position:absolute;inset:0}
  .logo{position:absolute;left:40px;top:118px;display:flex;align-items:center;gap:12px}
  .logo .mark{width:18px;height:18px;background:var(--red)}
  .logo .name{font-size:38px;font-weight:400;letter-spacing:10px;color:var(--black)}
  .person{position:absolute;right:34px;top:34px;text-align:right;color:var(--wine)}
  .person .given{font-size:24px;font-weight:700}
  .person .role{font-size:12px;color:var(--gray);margin-top:-2px}
  .person .family{font-size:24px;font-weight:700;margin-top:-2px}
  .person .title{font-size:13px;color:var(--ink);padding-bottom:4px;border-bottom:1px solid var(--rule)}
  .contact{position:absolute;left:40px;bottom:34px;width:250px;border-top:1px solid var(--rule);padding-top:8px;list-style:none}
  .contact li{display:flex;align-items:center;gap:10px;font-size:15px;color:var(--ink);line-height:21px}
  .contact svg{width:11px;height:11px;fill:var(--wine)}
</style>
</head>
<body>
<main class="stage">

  <section class="card card--back" aria-label="Reverso de la tarjeta">
    <svg class="base" viewBox="0 0 560 320" preserveAspectRatio="none" aria-hidden="true">
      <polygon points="0,280 250,280 265,262 375,262 392,280 392,278 560,200 560,320 0,320" fill="var(--paper-shade)"/>
      <polygon points="0,284 560,284 560,205 395,284 0,284 0,320 560,320 560,284" fill="var(--white)"/>
    </svg>
    <div class="brand">ULMIRA</div>
    <div class="social"><span class="dot"></span><span>@ulmiraAT</span></div>
  </section>

  <section class="card card--front" aria-label="Anverso de la tarjeta">
    <svg class="base" viewBox="0 0 560 320" preserveAspectRatio="none" aria-hidden="true">
      <polygon points="405,198 560,198 560,320 395,320" fill="var(--black)"/>
      <polygon points="420,178 560,178 560,262 410,262" fill="var(--wine)"/>
    </svg>
    <div class="logo"><span class="mark"></span><span class="name">ULMIRA</span></div>
    <div class="person">
      <div class="given">Gonzalo Pereda</div>
      <div class="role">COO</div>
      <div class="family">Mauricio Villalta</div>
      <div class="title">Director de Operaciones</div>
    </div>
    <ul class="contact">
      <li><svg viewBox="0 0 10 10"><path d="M2 0h2l1 3-1.5 1a6 6 0 0 0 2.5 2.5L7 5l3 1v2a2 2 0 0 1-2 2A8 8 0 0 1 0 2a2 2 0 0 1 2-2z"/></svg>(+571) 555 010 0199</li>
      <li><svg viewBox="0 0 10 10"><path d="M0 2h10v6H0zM1 3v.3l4 2.5 4-2.5V3L5 5.5z"/></svg>info@ulmira-example.com</li>
      <li><svg viewBox="0 0 10 10"><circle cx="5" cy="5" r="5"/></svg>www.ulmira-example.com</li>
    </ul>
  </section>

</main>
</body>
</html>
```